Card design for orthopaedic surgeons working as The Brightwater Joint Centre

Business cards, letterhead

Colors

Designer to choose colors to be used in the design.

Requirements
Must have
• Late addition.
• Cards letterhead must have logos of
• Crestmoor Lindell College of Surgeons
• Varenwood Bone Health Association
Nice to have
• Back of card to have space for appointment time to be added by hand and some blank space for writing incidental other notes.

```html
<!DOCTYPE html>
<html lang="en">
<head>
<meta charset="utf-8">
<title>The Brightwater Joint Centre — Business Card</title>
<link href="https://fonts.googleapis.com/css2?family=Poppins:wght@400;500;600&display=swap" rel="stylesheet">
<style>
  :root {
    --backdrop: #d9dadc;
    --navy: #021a33;
    --sky: #1e9cf6;
    --white: #ffffff;
    --badge: #e4eef7;
    --badge-edge: #b9cfe3;
    --card-shadow: 0 14px 30px rgba(0,0,0,0.22);
  }
  html, body {
    margin: 0;
    width: 1200px;
    height: 800px;
    overflow: hidden;
    background: var(--backdrop);
    font-family: "Poppins", sans-serif;
  }
  .canvas {
    position: relative;
    width: 1200px;
    height: 800px;
  }
  .card {
    position: absolute;
    top: 245px;
    width: 540px;
    height: 310px;
    border-radius: 22px;
    overflow: hidden;
    box-shadow: var(--card-shadow);
  }
  .card-front { left: 40px; background: var(--sky); }
  .card-back { left: 620px; background: var(--white); }

  .front-wave { position: absolute; inset: 0; }

  .wordmark {
    position: absolute;
    font-weight: 500;
    letter-spacing: -0.2px;
    white-space: nowrap;
  }
  .card-front .wordmark {
    left: 36px;
    top: 132px;
    font-size: 19px;
    color: var(--white);
  }
  .card-back .wordmark {
    left: 0;
    right: 0;
    top: 120px;
    text-align: center;
    font-size: 28px;
    color: var(--navy);
  }

  .holder {
    position: absolute;
    left: 26px;
    bottom: 26px;
    line-height: 1.15;
  }
  .holder-name {
    font-size: 17px;
    font-weight: 600;
    color: var(--sky);
  }
  .holder-role {
    font-size: 10px;
    color: var(--white);
  }

  .contact-list {
    position: absolute;
    right: 22px;
    top: 44px;
    margin: 0;
    padding: 0;
    list-style: none;
    color: var(--white);
    font-size: 10.5px;
    line-height: 17px;
    text-align: right;
  }
  .contact-list li {
    display: flex;
    justify-content: flex-end;
    align-items: center;
    gap: 7px;
  }
  .contact-list svg { width: 10px; height: 10px; fill: var(--navy); flex: none; }

  .address {
    position: absolute;
    right: 22px;
    bottom: 22px;
    font-size: 10.5px;
    color: var(--white);
  }

  .affiliations {
    position: absolute;
    left: 0;
    right: 0;
    bottom: 34px;
    display: flex;
    justify-content: center;
    gap: 28px;
  }
  .affiliation-badge {
    width: 44px;
    height: 44px;
    border-radius: 50%;
    background: var(--badge);
    border: 1.5px solid var(--badge-edge);
  }
</style>
</head>
<body>
<main class="canvas">

  <section class="card card-front" aria-label="Business card front">
    <svg class="front-wave" viewBox="0 0 540 310" preserveAspectRatio="none" aria-hidden="true">
      <path d="M0 0 H300 C345 0 372 55 362 115 C350 190 262 225 232 310 H0 Z" fill="var(--navy)"/>
    </svg>

    <div class="wordmark">The Brightwater Joint Centre</div>

    <div class="holder">
      <div class="holder-name">Daniel Harper</div>
      <div class="holder-role">President</div>
    </div>

    <ul class="contact-list">
      <li>555-214-7730
        <svg viewBox="0 0 10 10"><path d="M2 0.5 L3.8 2.6 L2.9 3.7 C3.6 5.2 4.8 6.4 6.3 7.1 L7.4 6.2 L9.5 8 L8.2 9.5 C4.2 9.2 0.8 5.8 0.5 1.8 Z"/></svg></li>
      <li>555-608-1942
        <svg viewBox="0 0 10 10"><rect x="0.5" y="2" width="9" height="6" rx="1"/></svg></li>
      <li>555-391-2586
        <svg viewBox="0 0 10 10"><rect x="2.5" y="0.5" width="5" height="9" rx="1"/></svg></li>
      <li>care@brightwater.example
        <svg viewBox="0 0 10 10"><rect x="0.5" y="2" width="9" height="6.5" rx="0.8"/></svg></li>
      <li>www.brightwater.example
        <svg viewBox="0 0 10 10"><circle cx="5" cy="5" r="4.5"/></svg></li>
    </ul>

    <div class="address">214 Harbour Road Kelford, Maine 04102
      <svg viewBox="0 0 10 10" width="10" height="10" style="fill:var(--navy);vertical-align:-1px;margin-left:5px"><path d="M5 0.5 C7.2 0.5 8.6 2.1 8.6 4 C8.6 6.3 5 9.5 5 9.5 C5 9.5 1.4 6.3 1.4 4 C1.4 2.1 2.8 0.5 5 0.5 Z"/></svg>
    </div>
  </section>

  <section class="card card-back" aria-label="Business card back">
    <div class="wordmark">The Brightwater Joint Centre</div>

    <div class="affiliations">
      <div class="affiliation-badge" role="img" aria-label="Crestmoor Lindell College of Surgeons membership badge"></div>
      <div class="affiliation-badge" role="img" aria-label="Varenwood Bone Health Association membership badge"></div>
    </div>
  </section>

</main>
</body>
</html>
```